Business Card Design Project

- makeup artist business card

- original and creative

- Elegant design

- Feel free to come out with cool designs but stick to being elegant and attractive

- Design relates to makeup

- includes name, occupation, contact numbers, email, website

- regular size business card

- round corner card

- double sided

- on 1 side it should just have the website name in the center " moonveilstudio.net "

Industry/Entity Type

Business

Requirements
Must have
• Delia Marsh
Makeup Artist
USA: +1 (415)772-0461
Singapore: +65 82307915
deliamarsh@moonveilstudio.net
www.moonveilstudio.net
Should not have
• nothing cartoon looking.
Pictures of makeup being grab from the internet.. Examples: eyes or lips.

```html
<!DOCTYPE html>
<html lang="en">
<head>
<meta charset="utf-8">
<title>Delia Marsh – Makeup Artist Business Card</title>
<link rel="stylesheet" href="https://fonts.googleapis.com/css2?family=Arimo&family=Tinos&display=swap">
<style>
  :root {
    --page-bg: #ecebee;
    --lilac: #b98ac6;
    --lilac-light: #cfaed8;
    --panel: #ffffff;
    --ink: #1c1a1e;
    --plum: #8e2a93;
    --shadow: rgba(60, 40, 70, 0.22);
    --photo-warm: #f5ec9a;
    --photo-soft: #f8f1d2;
  }
  * { box-sizing: border-box; margin: 0; padding: 0; }
  html, body {
    width: 1067px;
    height: 1200px;
    overflow: hidden;
    background: var(--page-bg);
  }
  .canvas {
    position: relative;
    width: 1067px;
    height: 1200px;
  }
  .card {
    position: absolute;
    left: 83px;
    width: 900px;
    height: 514px;
    border-radius: 36px;
    overflow: hidden;
    box-shadow: 0 10px 28px var(--shadow);
  }
  .card--front { top: 50px; }
  .card--back { top: 636px; }

  .card__pattern {
    position: absolute;
    inset: 0;
    background:
      radial-gradient(circle at 30% 30%, var(--lilac-light), transparent 60%),
      radial-gradient(circle at 75% 75%, var(--lilac-light), transparent 55%),
      var(--lilac);
  }

  /* Front side */
  .front__panel {
    position: absolute;
    left: 58px;
    top: 36px;
    right: 72px;
    bottom: 60px;
    background: var(--panel);
    box-shadow: 2px 3px 6px var(--shadow);
    overflow: hidden;
  }
  .front__photo {
    position: absolute;
    inset: 0 0 110px 0;
    background: linear-gradient(to right, var(--panel) 0%, var(--photo-soft) 25%, var(--photo-warm) 70%, var(--photo-soft) 100%);
    -webkit-mask-image: linear-gradient(to bottom, #000 55%, transparent);
            mask-image: linear-gradient(to bottom, #000 55%, transparent);
  }
  .front__identity {
    position: absolute;
    top: 18px;
    right: 22px;
    text-align: right;
  }
  .front__name {
    font-family: "Tinos", serif;
    font-size: 36px;
    font-weight: 400;
    color: var(--plum);
    line-height: 1.1;
  }
  .front__role {
    font-family: "Arimo", sans-serif;
    font-size: 18px;
    color: var(--ink);
    margin-top: 6px;
  }
  .front__contact {
    position: absolute;
    left: 22px;
    bottom: 16px;
    font-family: "Arimo", sans-serif;
    font-size: 22px;
    line-height: 1.45;
    list-style: none;
  }
  .front__contact .contact-phone { color: var(--ink); }
  .front__contact .contact-link { color: var(--plum); }

  /* Back side */
  .back__photo {
    position: absolute;
    left: 230px;
    top: 50px;
    width: 640px;
    height: 320px;
    border-radius: 50%;
    background: radial-gradient(ellipse at center, rgba(245, 236, 154, 0.55), transparent 70%);
  }
  .back__website {
    position: absolute;
    left: 0;
    right: 0;
    top: 224px;
    text-align: center;
    font-family: "Arimo", sans-serif;
    font-size: 44px;
    color: var(--ink);
  }
</style>
</head>
<body>
<main class="canvas">
  <section class="card card--front" aria-label="Business card front">
    <div class="card__pattern" role="img" aria-label="Lilac ornamental heart-and-leaf pattern"></div>
    <div class="front__panel">
      <div class="front__photo" role="img" aria-label="Close-up photograph of eyes with yellow eyeshadow"></div>
      <div class="front__identity">
        <h1 class="front__name">Delia Marsh</h1>
        <p class="front__role">Makeup Artist</p>
      </div>
      <ul class="front__contact">
        <li class="contact-phone">Phone USA: +1 (415)772-0461</li>
        <li class="contact-phone">Phone Singapore: +65 82307915</li>
        <li class="contact-link">deliamarsh@moonveilstudio.net</li>
        <li class="contact-link">www.moonveilstudio.net</li>
      </ul>
    </div>
  </section>

  <section class="card card--back" aria-label="Business card back">
    <div class="card__pattern" role="img" aria-label="Lilac ornamental heart-and-leaf pattern"></div>
    <div class="back__photo" role="img" aria-label="Faint photograph of eyes with yellow eyeshadow blended into the pattern"></div>
    <p class="back__website">www.moonveilstudio.net</p>
  </section>
</main>
</body>
</html>
```